We need 5-10 Instagram posts for a restaurant located in Dubai, UAE.

Background about the restaurant:

Forks and fizz is a boutique burgers and comfort food joint located at Dubai, UAE. We started operations in September 2016. The main focus on our food is for it to be simple, original and freshly made. The majority of our orders are take away with fewer people opting for dinning in. We connect with our customers through our Instagram account & our customers rely on it for updates.

The brief

What we are looking for is a vector design (advertisement) for multiple purposes including:

1. announcing that we started delivery
2. a post that we can use multiple times during the year just as a "reminder that we deliver"
3. posts that serve as an advertisement

posts need to be as simple as possible

for reference, our Instagram account is @forksandfizz

Colors
f04a50
ffffff
000000

Requirements
Should not have
• the designs should not have too many colors

```html
<!DOCTYPE html>
<html lang="en">
<head>
<meta charset="utf-8">
<title>Forks and fizz – Instagram posts</title>
<link href="https://fonts.googleapis.com/css2?family=Fredoka:wght@600&display=swap" rel="stylesheet">
<style>
  :root {
    --brand-red: #f04a50;
    --ink: #1d1d1d;
    --paper: #ffffff;
    --backdrop: #d8d8d8;
  }
  * { box-sizing: border-box; margin: 0; padding: 0; }
  html, body {
    width: 1200px;
    height: 1200px;
    overflow: hidden;
    background: var(--backdrop);
  }
  .post-set {
    position: absolute;
    top: 340px;
    left: 60px;
    display: flex;
    gap: 60px;
  }
  .post {
    width: 510px;
    height: 510px;
    background: var(--paper);
    display: flex;
    flex-direction: column;
    align-items: center;
    justify-content: center;
    box-shadow: 0 10px 24px rgba(0, 0, 0, 0.12);
  }
  .post__icon {
    display: block;
    margin-bottom: 14px;
  }
  .post__headline {
    font-family: "Fredoka", "Arial Rounded MT Bold", sans-serif;
    font-weight: 600;
    color: var(--ink);
    text-align: center;
    line-height: 0.9;
    letter-spacing: 0.5px;
  }
  .post--fresh .post__headline { font-size: 76px; }
  .post--burger .post__headline { font-size: 60px; }
</style>
</head>
<body>
  <main class="post-set">
    <section class="post post--fresh">
      <svg class="post__icon" width="70" height="180" viewBox="0 0 70 180"
           role="img" aria-label="Red spatula icon topped with flames">
        <rect x="0" y="0" width="70" height="180" rx="8" fill="#f04a50"/>
      </svg>
      <h2 class="post__headline">freshly<br>made</h2>
    </section>

    <section class="post post--burger">
      <svg class="post__icon" width="110" height="95" viewBox="0 0 110 95"
           role="img" aria-label="Red burger icon with a bite taken out">
        <rect x="0" y="0" width="110" height="95" rx="14" fill="#f04a50"/>
      </svg>
      <h2 class="post__headline">when life<br>throws<br>you a burger<br>eat it</h2>
    </section>
  </main>
</body>
</html>
```